Brightbay Orthodontics business card design

Need a business card design that reflects our re-branding (orthodontic office - braces) and a new partnership with a pediatric dental office. We would like to include "for adults and children" on the card as well so adults know they are welcome to get their braces here as well. Office design is modern and would like business card to reflect a modern type look. Here's the text we would like to be included on the card:

Darren Wolcott, DDS, MSD
5214 West Linden Avenue, Suite 204
Mansfield, TX 76991
555-418-2637
www.brightbayortho.example
info@brightbayortho.example

Can we add the following to the existing designs? Darren Wolcott, DDS, MSD 5214 West Linden Avenue, Suite 204 Mansfield, TX 76991 555-418-2637

Does anyone have any more vertical designs available? Thanks!

Dental

```html
<!DOCTYPE html>
<html lang="en">
<head>
<meta charset="utf-8">
<title>Brightbay Orthodontics Business Card</title>
<link href="https://fonts.googleapis.com/css2?family=Open+Sans:wght@400;600;700&display=swap" rel="stylesheet">
<style>
  :root {
    --page-bg: #e4e4e2;
    --card-white: #ffffff;
    --card-grey-light: #f4f4f4;
    --card-grey-dark: #c9c9c9;
    --card-black: #1d1b1c;
    --ink: #1f1f1f;
    --tagline: #555555;
    --name-blue: #1b7fc4;
    --detail-grey: #c8c8c8;
    --role-grey: #9a9a9a;
    --icon-green: #2ea043;
    --strip-yellow: #fff200;
    --strip-blue: #1b7fc4;
    --strip-magenta: #e6007e;
    --strip-green: #8dc63f;
    --strip-orange: #f7941d;
  }
  * { box-sizing: border-box; margin: 0; padding: 0; }
  html, body { width: 1200px; height: 871px; overflow: hidden; }
  body {
    background: var(--page-bg);
    font-family: "Open Sans", sans-serif;
    display: flex;
    flex-direction: column;
    align-items: center;
    justify-content: center;
    gap: 48px;
  }
  .card {
    width: 630px;
    height: 360px;
    border-radius: 3px;
    box-shadow: 0 6px 18px rgba(0,0,0,0.18);
    overflow: hidden;
    position: relative;
  }
  .card-front {
    background: radial-gradient(ellipse at 45% 30%, var(--card-grey-light) 0%, #e2e2e2 60%, var(--card-grey-dark) 100%);
    display: flex;
    align-items: center;
    justify-content: center;
  }
  .brand {
    display: flex;
    align-items: center;
    gap: 16px;
    color: var(--ink);
    font-weight: 700;
  }
  .brand-dot {
    width: 46px; height: 46px; border-radius: 50%;
    background: var(--ink);
    flex: none;
  }
  .brand-name { font-size: 44px; line-height: 1.05; }
  .tagline {
    display: block;
    margin-top: 10px;
    font-size: 16px;
    font-weight: 400;
    color: var(--tagline);
    letter-spacing: 0.5px;
  }
  .card-back { display: flex; background: var(--card-white); }
  .back-brand {
    width: 282px;
    display: flex;
    align-items: center;
    justify-content: center;
    padding-left: 10px;
  }
  .back-brand .brand { gap: 10px; }
  .back-brand .brand-dot { width: 26px; height: 26px; }
  .back-brand .brand-name { font-size: 25px; }
  .back-brand .tagline { font-size: 11px; margin-top: 6px; }
  .color-strip { width: 16px; display: flex; flex-direction: column; }
  .color-strip span { flex: 1; }
  .color-strip .yellow { background: var(--strip-yellow); }
  .color-strip .blue { background: var(--strip-blue); }
  .color-strip .magenta { background: var(--strip-magenta); }
  .color-strip .green { background: var(--strip-green); }
  .color-strip .orange { background: var(--strip-orange); }
  .details {
    flex: 1;
    background: var(--card-black);
    padding: 58px 0 0 32px;
    color: var(--detail-grey);
    font-size: 14px;
    letter-spacing: 0.4px;
  }
  .person-name { color: var(--name-blue); font-weight: 700; font-size: 19px; letter-spacing: 1px; }
  .person-role { color: var(--role-grey); font-size: 10px; margin-top: 2px; }
  .address { margin-top: 20px; line-height: 1.5; }
  .contact-list { list-style: none; margin-top: 20px; line-height: 1.65; }
  .contact-list li { display: flex; align-items: center; gap: 14px; }
  .contact-list svg { width: 13px; height: 13px; flex: none; }
</style>
</head>
<body>
  <section class="card card-front" aria-label="Card front">
    <div class="brand">
      <span class="brand-dot"></span>
      <span class="brand-name">Brightbay<br>Orthodontics<span class="tagline">for adults and children</span></span>
    </div>
  </section>

  <section class="card card-back" aria-label="Card back">
    <div class="back-brand">
      <div class="brand">
        <span class="brand-dot"></span>
        <span class="brand-name">Brightbay<br>Orthodontics<span class="tagline">for adults and children</span></span>
      </div>
    </div>
    <div class="color-strip">
      <span class="yellow"></span><span class="blue"></span><span class="magenta"></span><span class="green"></span><span class="orange"></span>
    </div>
    <div class="details">
      <p class="person-name">Darren Wolcott</p>
      <p class="person-role">DDS, MSD</p>
      <p class="address">5214 West Linden Avenue, Suite 204<br>Mansfield, TX 76991</p>
      <ul class="contact-list">
        <li>
          <svg viewBox="0 0 16 16" aria-hidden="true"><path fill="var(--icon-green)" d="M3 1h3l1.5 4-2 1.2a9 9 0 0 0 4.3 4.3L11 8.5l4 1.5v3a2 2 0 0 1-2 2A13 13 0 0 1 1 3a2 2 0 0 1 2-2z"/></svg>
          555-418-2637
        </li>
        <li>
          <svg viewBox="0 0 16 16" aria-hidden="true"><rect x="1" y="3" width="14" height="10" fill="none" stroke="var(--icon-green)" stroke-width="1.6"/><path d="M1 3l7 6 7-6" fill="none" stroke="var(--icon-green)" stroke-width="1.6"/></svg>
          info@brightbayortho.example
        </li>
        <li>
          <svg viewBox="0 0 16 16" aria-hidden="true"><circle cx="8" cy="8" r="6.5" fill="none" stroke="var(--icon-green)" stroke-width="1.5"/><ellipse cx="8" cy="8" rx="2.8" ry="6.5" fill="none" stroke="var(--icon-green)" stroke-width="1.2"/><path d="M1.5 8h13" stroke="var(--icon-green)" stroke-width="1.2"/></svg>
          www.brightbayortho.example
        </li>
      </ul>
    </div>
  </section>
</body>
</html>
```